Wattle Ridge Hours needing a box to hold our gorgeous hand poured candles that look high end.

We need a packaging design that showcases our gorgeous candles.
Would like whole box in turquoise with a black band around bottom with a thin silver separating the two and also silver band around very top as per image attached.
Our feature color is turquoise, silver , white and black.
With the current logo like the font but want it bolder. Please do in black with 'hours' in silver or white. Can I also see 'Wattle Ridg'e in white with 'hours' in silver just too see which stands out more.
Would like the blue butterfly image to top right of the 'er' in Ridge. Can play with the design around the picture but would like the same shape of butterfly. Could be solid or just outline image.
Wattle Ridge Hours will over time involve into selling of body care products, skincare, food, wood work will be used on alot of branding so if this can be kept in mind thank you.
Box measurements 10cm width, 13cm height, depth 10cm. Hope it makes sense.

Target Market(s)

Tourism travellers from overseas wanting to take home a gift from the area they have visited

Industry/Entity Type

Work

Font styles to use
Script

Requirements
Must have
• Turquoise box with black band around bottom with thin silver seperating black and turquoise and also around very top of box as per the box picture attached.
Logo with single butterfly to top right. Please do font bolder and do in black and an image in white with the word hours in white (if black font) with hours in silver just want to see
Nice to have
• A butterfly insignia...would like someone to design a different concept of a butterfly ie. half of bold then light or abstract just something outside of the box idea not like all the ones you can just download from websites please thank you.
Should not have
• Too busy

```html
<!DOCTYPE html>
<html lang="en">
<head>
<meta charset="utf-8">
<title>Wattle Ridge Hours – Candle Box Panels</title>
<link rel="stylesheet" href="https://fonts.googleapis.com/css2?family=Marcellus&family=Tinos&display=swap">
<style>
  :root {
    --stage: #e6e7e9;
    --turquoise-deep: #1597cf;
    --turquoise-mid: #27b9e2;
    --turquoise-light: #4fdcef;
    --silver: #eef1f3;
    --silver-edge: #c9cfd4;
    --band-black: #050607;
    --ink: #07141c;
    --wordmark: #ffffff;
    --divider: rgba(7, 20, 28, 0.55);
  }
  * { box-sizing: border-box; margin: 0; padding: 0; }
  html, body {
    width: 1200px;
    height: 960px;
    overflow: hidden;
    background: var(--stage);
  }
  .dieline {
    position: absolute;
    left: 160px;
    top: 130px;
    display: flex;
    gap: 0;
    box-shadow: 0 18px 40px rgba(0, 0, 0, 0.18);
  }
  .panel {
    position: relative;
    width: 440px;
    height: 710px;
    display: flex;
    flex-direction: column;
    border-right: 1px solid rgba(0, 0, 0, 0.08);
  }
  .band-silver-top {
    height: 12px;
    background: linear-gradient(180deg, #ffffff, var(--silver) 60%, var(--silver-edge));
  }
  .turquoise-field {
    position: relative;
    flex: 1;
    background:
      radial-gradient(ellipse at 30% 20%, rgba(255, 255, 255, 0.12), transparent 55%),
      linear-gradient(180deg, var(--turquoise-deep) 0%, var(--turquoise-mid) 45%, var(--turquoise-light) 100%);
  }
  .band-silver-divider {
    height: 11px;
    background: linear-gradient(180deg, var(--silver-edge), #ffffff 45%, var(--silver));
  }
  .band-black {
    height: 94px;
    background: linear-gradient(180deg, #16181a, var(--band-black) 40%);
  }
  .band-silver-bottom {
    height: 10px;
    background: linear-gradient(180deg, var(--silver), #ffffff 50%, var(--silver-edge));
  }

  /* Wordmark */
  .wordmark {
    position: absolute;
    display: flex;
    align-items: center;
    gap: 12px;
    font-family: "Marcellus", serif;
    color: var(--wordmark);
    letter-spacing: 0.5px;
    white-space: nowrap;
  }
  .wordmark-dot {
    border-radius: 50%;
    background: var(--wordmark);
    flex-shrink: 0;
  }
  .front .wordmark {
    top: 150px;
    left: 0;
    right: 0;
    justify-content: center;
    font-size: 36px;
  }
  .front .wordmark-dot { width: 16px; height: 16px; }
  .side .wordmark {
    top: 68px;
    left: 0;
    right: 0;
    justify-content: center;
    font-size: 22px;
    gap: 8px;
  }
  .side .wordmark-dot { width: 10px; height: 10px; }

  /* Front content */
  .headline {
    position: absolute;
    top: 322px;
    left: 0;
    right: 0;
    text-align: center;
    font-family: "Marcellus", serif;
    font-size: 36px;
    color: var(--ink);
    letter-spacing: 0.3px;
  }
  .divider-ornament {
    position: absolute;
    left: 50%;
    transform: translateX(-50%);
    height: 14px;
    border-radius: 7px;
    background: var(--divider);
  }
  .front .divider-ornament { top: 399px; width: 210px; }
  .side .divider-ornament { top: 540px; width: 150px; height: 12px; }
  .front-copy {
    position: absolute;
    top: 462px;
    left: 60px;
    right: 60px;
    text-align: center;
    font-family: "Tinos", serif;
    font-size: 15px;
    line-height: 20px;
    color: var(--ink);
  }

  /* Side content */
  .side-copy {
    position: absolute;
    top: 180px;
    left: 52px;
    right: 40px;
    font-family: "Tinos", serif;
    font-size: 12px;
    line-height: 17.2px;
    color: var(--ink);
    text-align: justify;
    text-align-last: center;
  }
</style>
</head>
<body>
  <main class="dieline">
    <section class="panel front">
      <div class="band-silver-top"></div>
      <div class="turquoise-field">
        <div class="wordmark">
          <span>Wattle Ridge Hours</span>
          <span class="wordmark-dot"></span>
        </div>
        <h1 class="headline">LOREM IPSUM DOLOR</h1>
        <div class="divider-ornament" role="img" aria-label="Flowing swirl divider ornament"></div>
        <p class="front-copy">Lorem ipsum dolor sit amet, consectetur adipisicing elit, sed do eiusmod tempor incididunt ut labore et dolore magna aliqua.</p>
      </div>
      <div class="band-silver-divider"></div>
      <div class="band-black"></div>
      <div class="band-silver-bottom"></div>
    </section>

    <section class="panel side">
      <div class="band-silver-top"></div>
      <div class="turquoise-field">
        <div class="wordmark">
          <span>Wattle Ridge Hours</span>
          <span class="wordmark-dot"></span>
        </div>
        <p class="side-copy">Lorem ipsum dolor sit amet, consectetur adipisicing elit, sed do eiusmod tempor incididunt ut labore et dolore magna aliqua. Lorem ipsum dolor sit amet, consectetur adipisicing elit, sed do eiusmod tempor incididunt ut labore et dolore magna aliqua. Lorem ipsum dolor sit amet, consectetur adipisicing elit, sed do eiusmod tempor incididunt ut labore et dolore magna aliqua. Lorem ipsum dolor sit amet, consectetur adipisicing elit, sed do eiusmod tempor incididunt ut labore et dolore magna aliqua. Lorem ipsum dolor sit amet, consectetur adipisicing elit, sed do eiusmod tempor incididunt ut labore et dolore magna aliqua. Lorem ipsum dolor sit amet, consectetur adipisicing elit, sed do eiusmod tempor incididunt ut labore et dolore magna aliqua. Lorem ipsum dolor sit amet, consectetur adipisicing elit, sed do eiusmod tempor incididunt ut labore et dolore magna aliqua.</p>
        <div class="divider-ornament" role="img" aria-label="Flowing swirl divider ornament"></div>
      </div>
      <div class="band-silver-divider"></div>
      <div class="band-black"></div>
      <div class="band-silver-bottom"></div>
    </section>
  </main>
</body>
</html>
```